Professional looking Roller Blind Discount Card that portrays quality at a value for money price!

We need a double sided business card designed as a discount card. Size 90mm wide x 55mm high.We would like it to look professional and portray quality at a value for money price point.I have uploaded a word document with a basic layout with the information we want included on each side of the card. Please put your own thought into the layout.

Contact Information for Business Card

As per word document attached.

```html
<!DOCTYPE html>
<html lang="en">
<head>
<meta charset="utf-8">
<title>Roller Blinds Discount Card</title>
<link href="https://fonts.googleapis.com/css2?family=EB+Garamond:wght@400;500;600&family=Roboto+Condensed:wght@700;900&display=swap" rel="stylesheet">
<style>
  :root {
    --blue: #27a7df;
    --ink: #1b1b1b;
    --white: #ffffff;
    --stage: #dcdde0;
    --curve-grey: #c9cacc;
    --gold: #e2b43a;
    --gold-deep: #b8841c;
    --seal-red: #b3141c;
    --seal-text-red: #a8121a;
    --seal-cream: #fff3d6;
  }
  * { box-sizing: border-box; margin: 0; padding: 0; }
  html, body { width: 1200px; height: 800px; overflow: hidden; }
  body {
    background: var(--stage);
    font-family: "EB Garamond", Georgia, serif;
    color: var(--ink);
    position: relative;
  }
  .card {
    position: absolute;
    left: 320px;
    width: 560px;
    height: 342px;
    background: var(--white);
    overflow: hidden;
    box-shadow: 0 6px 18px rgba(0,0,0,0.18);
  }
  .card--front { top: 36px; }
  .card--back { top: 418px; }

  /* Front */
  .front-bg { position: absolute; inset: 0; }
  .discount {
    position: absolute; left: 26px; top: 4px;
    color: var(--blue); display: flex; align-items: flex-start;
  }
  .discount__num { font-size: 118px; line-height: 1; font-weight: 400; letter-spacing: -2px; }
  .discount__tail { display: flex; flex-direction: column; margin-left: 2px; margin-top: 24px; }
  .discount__pct { font-size: 38px; line-height: 0.9; }
  .discount__off { font-size: 44px; line-height: 0.9; letter-spacing: 1px; }
  .headline {
    position: absolute; right: 24px; top: 36px; width: 272px; text-align: right;
  }
  .headline__quality { font-size: 34px; font-variant: small-caps; line-height: 1; letter-spacing: 1px; }
  .headline__custom { font-size: 22px; font-variant: small-caps; line-height: 1; letter-spacing: 1px; margin-top: -2px; }
  .headline__product {
    font-size: 25px; color: var(--blue); letter-spacing: 1px; line-height: 1.1;
    border-bottom: 1.5px solid var(--blue); padding-bottom: 2px; margin-top: 2px;
  }
  .headline__types { font-size: 15px; margin-top: 4px; letter-spacing: 0.5px; }

  .seal {
    position: absolute; border-radius: 50%;
    display: flex; flex-direction: column; align-items: center; justify-content: center;
    font-family: "Roboto Condensed", Arial, sans-serif; font-weight: 900;
    text-align: center; line-height: 0.95; text-transform: uppercase;
  }
  .seal--gold {
    background: radial-gradient(circle, var(--seal-cream) 0%, var(--gold) 62%, var(--gold-deep) 100%);
    color: var(--seal-text-red);
  }
  .seal--red {
    background: radial-gradient(circle, var(--seal-red) 60%, var(--gold) 62%, var(--gold-deep) 100%);
    color: var(--white);
  }
  .seal--measure { left: 48px; top: 150px; width: 104px; height: 104px; }
  .seal--price { left: 222px; top: 178px; width: 104px; height: 104px; }
  .seal--family { left: 410px; top: 194px; width: 100px; height: 100px; }
  .seal__small { font-size: 11px; font-weight: 700; }
  .seal__big { font-size: 19px; }
  .seal__mid { font-size: 14px; }
  .seal__ribbon {
    background: var(--gold); color: var(--ink); font-size: 15px;
    padding: 2px 8px; margin-top: 3px;
  }
  .seal--measure .seal__big { color: var(--ink); margin-top: 2px; }

  .call {
    position: absolute; font-size: 30px; letter-spacing: 0.5px; white-space: nowrap;
  }
  .call--front { left: 0; right: 0; bottom: 14px; text-align: center; color: var(--white); }
  .call__number { font-weight: 600; }

  /* Back */
  .band { position: absolute; background: var(--blue); }
  .band--left { left: 0; top: 92px; width: 320px; height: 62px; }
  .band--right { left: 300px; top: 166px; width: 260px; height: 96px; }
  .back-title {
    position: absolute; left: 0; right: 0; top: 12px; text-align: center;
    color: var(--blue); font-size: 50px; letter-spacing: 2px; line-height: 1; font-weight: 500;
  }
  .back-sub {
    position: absolute; left: 0; right: 0; top: 62px; text-align: center;
    font-size: 22px; letter-spacing: 0.5px;
  }
  .photo {
    position: absolute; left: 28px; top: 96px; width: 272px; height: 164px;
    background: linear-gradient(135deg, #7c7064 0%, #5f7a4a 30%, #8fae6c 60%, #c9c3b8 100%);
  }
  .fabrics {
    position: absolute; left: 300px; top: 172px; width: 260px; text-align: center;
    color: var(--white); font-size: 27px; line-height: 1.02;
  }
  .call--back { left: 24px; top: 272px; font-size: 29px; }
  .call--back .call__number { color: var(--blue); }
  .brand {
    position: absolute; left: 350px; width: 190px; top: 272px;
    display: flex; flex-direction: column; align-items: center; gap: 6px;
    color: var(--blue); font-size: 19px; letter-spacing: 1px; white-space: nowrap;
  }
  .brand__mark { width: 26px; height: 26px; background: var(--blue); }
</style>
</head>
<body>
  <section class="card card--front" aria-label="Card front">
    <svg class="front-bg" width="560" height="342" viewBox="0 0 560 342" aria-hidden="true">
      <path d="M0,160 Q200,232 380,222 T560,206 L560,342 L0,342 Z" fill="var(--curve-grey)"/>
      <path d="M0,172 Q200,244 380,234 T560,218 L560,342 L0,342 Z" fill="var(--blue)"/>
    </svg>
    <div class="discount">
      <span class="discount__num">25</span>
      <span class="discount__tail"><span class="discount__pct">%</span><span class="discount__off">OFF</span></span>
    </div>
    <div class="headline">
      <div class="headline__quality">Quality</div>
      <div class="headline__custom">Custom Made</div>
      <div class="headline__product">ROLLER BLINDS</div>
      <div class="headline__types">Blockout | Screen | Light Filtering</div>
    </div>
    <div class="seal seal--gold seal--measure">
      <span class="seal__small">In Home</span>
      <span class="seal__small">Measure &amp;</span>
      <span class="seal__small">Quote</span>
      <span class="seal__big">Free</span>
    </div>
    <div class="seal seal--red seal--price">
      <span class="seal__big">Best</span>
      <span class="seal__big">Price</span>
      <span class="seal__ribbon">Guarantee</span>
    </div>
    <div class="seal seal--red seal--family">
      <span class="seal__mid">Owned</span>
      <span class="seal__mid">And</span>
      <span class="seal__mid">Operated</span>
      <span class="seal__ribbon">Family</span>
    </div>
    <p class="call call--front">Call <span class="call__number">0400 555 210</span> Today</p>
  </section>

  <section class="card card--back" aria-label="Card back">
    <div class="band band--left"></div>
    <div class="band band--right"></div>
    <h1 class="back-title">ROLLER BLINDS</h1>
    <p class="back-sub">FREE in Home Measure &amp; Quote</p>
    <div class="photo" role="img" aria-label="Photo of a kitchen window with roller blinds looking out onto a garden"></div>
    <p class="fabrics">Huge<br>Selection<br>Of Fabrics</p>
    <p class="call call--back">Call <span class="call__number">0400 555 210</span> Today</p>
    <div class="brand"><span class="brand__mark"></span><span class="brand__name">BRAMWELL BLINDS</span></div>
  </section>
</body>
</html>
```